Tolbek cards

I want a simple business card that pops.
Logo on one side.
On side two i want.
"Are you thinking about a new building on your property, or renovating an existing structure? Contact".....
Owners Name: Dale Whitacre
Owners Phone number: 610-555-0187
Address:4076 Copper Ridge RD, Corvale, PA 16099
Committed to Quality, Service, and Integrity

```html
<!DOCTYPE html>
<html lang="en">
<head>
<meta charset="utf-8">
<title>Tolbek Builders LLC – Business Card</title>
<link href="https://fonts.googleapis.com/css2?family=Roboto:wght@400;500;700&family=Montserrat:wght@500&display=swap" rel="stylesheet">
<style>
  :root {
    --brown: #412c1c;
    --ink: #111111;
    --paper: #ffffff;
    --backdrop: #f0f0f0;
  }
  * { margin: 0; padding: 0; box-sizing: border-box; }
  html, body {
    width: 1200px; height: 990px; overflow: hidden;
    background: var(--backdrop);
    font-family: "Roboto", Arial, sans-serif;
  }
  .card {
    position: absolute; left: 244px; width: 712px; height: 407px;
    border-radius: 40px; background: var(--paper); overflow: hidden;
    box-shadow: 0 8px 22px rgba(0,0,0,0.28);
  }
  .card--front { top: 68px; }
  .card--back { top: 516px; }

  /* Front */
  .brand {
    position: absolute; inset: 0;
    display: flex; flex-direction: column; align-items: center; justify-content: center;
    color: var(--brown); font-weight: 700;
  }
  .brand__mark { width: 62px; height: 62px; background: var(--brown); margin-bottom: 26px; }
  .brand__name { font-size: 88px; line-height: 1; letter-spacing: 1px; text-transform: uppercase; }
  .brand__sub { font-size: 30px; line-height: 1; margin-top: 12px; letter-spacing: 1px; text-transform: uppercase; }

  /* Back */
  .band { position: absolute; left: 0; right: 0; background: var(--brown); color: var(--paper);
    display: flex; align-items: center; justify-content: center; text-align: center; font-weight: 500; }
  .band--top { top: 0; height: 72px; font-size: 19px; letter-spacing: 0.5px; }
  .band--bottom { bottom: 0; height: 92px; font-size: 19.5px; line-height: 26px; padding: 0 20px; letter-spacing: 0.5px; }
  .contact { position: absolute; left: 0; right: 0; top: 124px; text-align: center; }
  .contact__name { font-size: 43px; font-weight: 700; color: var(--brown); line-height: 1; letter-spacing: 0.5px; }
  .contact__role { font-family: "Montserrat", Arial, sans-serif; font-weight: 500; font-size: 19px; color: var(--ink); line-height: 1; margin-top: 2px; }
  .contact__divider { display: block; margin: 3px auto 0; }
  .contact__line { font-size: 18px; font-weight: 500; color: var(--ink); letter-spacing: 0.8px; line-height: 26px; }
  .contact__line--phone { margin-top: 2px; }
</style>
</head>
<body>
  <section class="card card--front">
    <div class="brand">
      <div class="brand__mark"></div>
      <div class="brand__name">Tolbek</div>
      <div class="brand__sub">Builders LLC</div>
    </div>
  </section>

  <section class="card card--back">
    <div class="band band--top">Committed to Quality, Service, and Integrity</div>
    <div class="contact">
      <h1 class="contact__name">Dale Whitacre</h1>
      <p class="contact__role">Owners</p>
      <svg class="contact__divider" width="300" height="26" viewBox="0 0 300 26" aria-hidden="true">
        <g fill="var(--brown)">
          <circle cx="3" cy="13" r="2.5"/><circle cx="20" cy="13" r="3.2"/><circle cx="37" cy="13" r="4"/>
          <circle cx="54" cy="13" r="4.8"/><circle cx="71" cy="13" r="5.6"/><circle cx="88" cy="13" r="6.4"/>
          <circle cx="104" cy="13" r="7"/>
          <circle cx="134" cy="13" r="12"/><circle cx="166" cy="13" r="12"/>
          <circle cx="196" cy="13" r="7"/><circle cx="212" cy="13" r="6.4"/><circle cx="229" cy="13" r="5.6"/>
          <circle cx="246" cy="13" r="4.8"/><circle cx="263" cy="13" r="4"/><circle cx="280" cy="13" r="3.2"/>
          <circle cx="297" cy="13" r="2.5"/>
        </g>
        <path d="M129 7 l3 0 l1.5 3.5 l-2 1.5 q1.5 3 4.5 4.5 l1.5 -2 l3.5 1.5 l0 3 q-7 1 -12 -12z" fill="var(--paper)"/>
        <path d="M166 20 q-5 -6 -5 -10 a5 5 0 0 1 10 0 q0 4 -5 10z" fill="none" stroke="var(--paper)" stroke-width="1.4"/>
        <circle cx="166" cy="10" r="1.8" fill="var(--paper)"/>
      </svg>
      <p class="contact__line contact__line--phone">610-555-0187</p>
      <p class="contact__line">4076 Copper Ridge RD, Corvale, PA 16099</p>
    </div>
    <div class="band band--bottom">"Are you thinking about a new building on your property, or renovating an existing structure? Contact".....</div>
  </section>
</body>
</html>
```